Wedding Ceremony Equipment Hire Business Card

I need a business card design for a new business I created called Vowline Rentals. We hire out Wedding Ceremony equipment and decorations mainly for beach and garden wedding ceremonies that include delivery, set up and dismantle. We do offer DIY Chair Hire as well.
I'd like to have a similar design and colours to our website:
www.vowlinerentals.com.au
If possible would like the front to incorporate our information and logo and the back to have two faded example pictures of our wedding ceremonies.
I have attached two photos and our logo. Please let me know if you need a better pic of our logo though.

Target Market(s)

Newly engaged couples, aged 25 and upwards

Industry/Entity Type

Wedding

Contact Information for Business Card

Vowline Rentals
Mira Holt
0412 908 146
hello@vowlinerentals.com.au
www.vowlinesocial.com/VowlineRentals

```html
<!DOCTYPE html>
<html lang="en">
<head>
<meta charset="utf-8">
<title>Vowline Rentals – Business Card</title>
<link rel="stylesheet" href="https://fonts.googleapis.com/css2?family=Tinos&display=swap">
<style>
  :root {
    --charcoal: #2a2a2a;
    --mint: #80d6b6;
    --mint-soft: #b9ecd9;
    --mint-text: #8fe3c3;
    --name-light: #e6fbf2;
    --ink: #1f1f1f;
    --white: #ffffff;
    --backdrop: #ecebe7;
    --sky: #2f6fd6;
    --sand: #c98a4e;
    --lawn: #4f8a34;
    --sky-light: #8cc4ef;
  }
  * { box-sizing: border-box; margin: 0; padding: 0; }
  html, body {
    width: 1200px; height: 750px; overflow: hidden;
    background: var(--backdrop);
    font-family: "Tinos", "Times New Roman", serif;
  }
  .stage { position: relative; width: 1200px; height: 750px; }

  .card {
    position: absolute;
    width: 620px; height: 355px;
    background: var(--charcoal);
    overflow: hidden;
    box-shadow: 0 6px 18px rgba(0,0,0,.25);
  }

  /* Back of card */
  .card--back { left: 40px; top: 40px; }
  .back__strip {
    position: absolute; left: 0; right: 0; top: 78px; height: 206px;
    border-top: 5px solid var(--white);
    border-bottom: 5px solid var(--white);
    display: flex;
  }
  .back__accent {
    position: absolute; left: 300px; right: 0; top: 70px; height: 8px;
    background: var(--mint-soft);
  }
  .photo { flex: 1; height: 100%; }
  .photo--beach {
    background: linear-gradient(180deg, var(--sky) 0%, #4c8fe0 32%, #d8a46a 48%, var(--sand) 100%);
  }
  .photo--garden {
    background: linear-gradient(180deg, var(--sky-light) 0%, #a9d6f2 22%, #6fa85a 42%, var(--lawn) 100%);
  }
  .back__brand {
    position: absolute; left: 0; right: 0; top: 160px;
    text-align: center;
    font-size: 34px; color: var(--ink);
    letter-spacing: 1px;
  }

  /* Front of card */
  .card--front { left: 540px; top: 355px; }
  .front__band {
    position: absolute; left: 0; right: 0; top: 100px; height: 150px;
    background: var(--mint);
  }
  .front__flourish {
    position: absolute; right: 0; top: 0; width: 260px; height: 100%;
    background: linear-gradient(90deg, rgba(255,255,255,0) 0%, rgba(255,255,255,.28) 100%);
  }
  .front__brand {
    position: absolute; left: 250px; top: 120px;
    font-size: 38px; line-height: 44px; color: var(--ink);
    letter-spacing: 1px;
  }
  .front__name {
    position: absolute; left: 280px; width: 260px; top: 190px;
    text-align: center;
    font-size: 24px; line-height: 28px; color: var(--name-light);
  }
  .front__rule {
    position: absolute; left: 290px; width: 240px; top: 236px;
    height: 2px; background: var(--white);
  }
  .front__contact {
    position: absolute; left: 270px; width: 280px; top: 262px;
    list-style: none; text-align: center;
    font-size: 13px; line-height: 18px; color: var(--mint-text);
  }
</style>
</head>
<body>
<main class="stage">

  <section class="card card--back" aria-label="Card back">
    <div class="back__accent"></div>
    <div class="back__strip">
      <div class="photo photo--beach" role="img" aria-label="Photo of a beach wedding ceremony with white chairs lining a sandy aisle"></div>
      <div class="photo photo--garden" role="img" aria-label="Photo of a harbourside garden wedding ceremony with white chairs and a white aisle runner"></div>
    </div>
    <p class="back__brand">Vowline Rentals</p>
  </section>

  <section class="card card--front" aria-label="Card front">
    <div class="front__band">
      <div class="front__flourish" role="img" aria-label="Soft decorative swirl pattern"></div>
    </div>
    <p class="front__brand">Vowline Rentals</p>
    <p class="front__name">Mira Holt</p>
    <div class="front__rule"></div>
    <ul class="front__contact">
      <li>Call us: 0412 908 146</li>
      <li>hello@vowlinerentals.com.au</li>
      <li>www.vowlinerentals.com.au</li>
      <li>www.vowlinesocial.com/VowlineRentals</li>
    </ul>
  </section>

</main>
</body>
</html>
```